Design a product reviews website

We need a website design and simple logo for the brand Venlotix.com. The website will provide reviews of technology products and services. The brand and website should be approachable but should also be trustworthy and high quality. The deliverable should be designs, specs and assets that I can provide to a development team to build the website.

Target Market(s)

People researching products to buy.

Industry/Entity Type

Product

Logo Text

Venlotix.com

Number of Pages Required

5+ page

Font styles to use
Sans Serif

Colors
0492cd
0355a3
3176b5
33a6d7
85cae6
85abd2
cedeed
cee9f5

Requirements
Must have
• - Designs for the Homepage, Category and Article pages.
• - Designs for web and mobile.
• - Designs details for the engineering team to use for development.
• - I'm open to other colors than the preferences I chose but I'm more likely to like blues, greys and blacks.

```html
<!DOCTYPE html>
<html lang="en">
<head>
<meta charset="utf-8">
<title>Venlotix — Product and Service Reviews</title>
<link href="https://fonts.googleapis.com/css2?family=Open+Sans:wght@400;600;700&display=swap" rel="stylesheet">
<style>
:root{
  --blue-deep:#0355a3;
  --blue-main:#0492cd;
  --blue-mid:#3176b5;
  --blue-bright:#33a6d7;
  --blue-soft:#85cae6;
  --heading:#1f5fa6;
  --text:#333;
  --muted:#8a8a8a;
  --line:#e1e1e1;
  --footer:#262626;
  --footer-bottom:#1b1b1b;
  --footer-text:#b9b9b9;
  --white:#fff;
}
*{margin:0;padding:0;box-sizing:border-box}
html,body{width:1200px;height:2571px;overflow:hidden;background:var(--white);font-family:"Open Sans",Arial,sans-serif;color:var(--text)}
.page{position:relative;width:1200px;height:2571px}
.abs{position:absolute}

/* hero */
.hero{left:0;top:0;width:1200px;height:440px;background:linear-gradient(100deg,#0b4f9c 0%,#1266b8 35%,#2a7fce 60%,#1a6cbf 100%)}
.hero-shade{left:0;top:0;width:1200px;height:440px;background:radial-gradient(ellipse at 72% 40%,rgba(120,180,240,.35),rgba(0,0,0,0) 55%)}
.menu-btn{left:9px;top:26px;width:41px;height:44px;border:1.5px solid rgba(255,255,255,.85);border-radius:3px;display:flex;flex-direction:column;justify-content:center;align-items:center;gap:5px}
.menu-btn span{width:20px;height:3px;background:var(--white)}
.brand{left:134px;top:30px;height:44px;display:flex;align-items:center;gap:10px}
.brand-dot{width:34px;height:34px;border-radius:50%;background:#f2c21b}
.brand-name{font-size:36px;font-weight:600;color:var(--white);letter-spacing:-.5px}
.search{left:460px;top:29px;width:280px;height:41px;display:flex;background:var(--white)}
.search-input{flex:1;font-size:11px;color:#999;padding:0 14px;line-height:41px}
.search-btn{width:38px;height:41px;background:#3a3a3a;display:flex;align-items:center;justify-content:center}
.hero-copy{left:0;top:182px;width:1200px;text-align:center;color:var(--white)}
.hero-copy .lead{font-size:32px;font-weight:400;line-height:40px}
.hero-copy .title{font-size:35px;font-weight:700;line-height:44px;letter-spacing:.3px}
.hero-actions{left:507px;top:266px;display:flex;gap:8px}
.hero-btn{height:40px;background:var(--white);color:var(--blue-deep);font-size:13px;font-weight:600;display:flex;align-items:center;justify-content:center;border-radius:2px}
.hero-dots{left:558px;top:410px;display:flex;gap:16px}
.hero-dots span{width:9px;height:9px;border-radius:50%;border:1.5px solid var(--white)}
.hero-dots span.on{background:var(--white)}

/* sidebar */
.sidebar{left:132px;top:486px;width:163px;box-shadow:6px 0 8px -6px rgba(0,0,0,.18)}
.cat{height:48px;display:flex;align-items:center;gap:12px;font-size:13.5px;font-weight:600;color:#555;border-bottom:1px solid #f1f1f1;padding-left:2px}
.cat.active{color:var(--blue-deep)}
.cat svg{width:14px;height:14px;flex:none}

/* headings */
.section-title{font-size:24px;font-weight:700;color:var(--heading)}

/* feature blocks */
.feature{left:327px;width:472px}
.feature-media{width:472px;height:281px;position:relative}
.tag{position:absolute;width:26px;height:26px;background:var(--blue-bright);display:flex;align-items:center;justify-content:center}
.feature-text{margin-top:16px;font-size:14.5px;line-height:20px;color:#333}
.author{margin-top:8px;display:flex;align-items:center;gap:10px;height:36px}
.avatar{width:36px;height:36px;border-radius:50%}
.author-name{font-size:11px;color:#333;line-height:15px}
.author-date{font-size:9.5px;color:var(--muted);line-height:13px}
.minis{margin-top:11px;display:flex;gap:17px}
.mini{width:146px;height:161px;border:1px solid #ddd;padding:4px}
.mini-media{height:96px;position:relative}
.mini-text{font-size:10px;line-height:14px;color:var(--muted);padding:12px 8px 0}

/* popular */
.popular{left:826px;width:240px}
.pop-media{width:240px;height:160px;position:relative}
.pop-text{margin-top:9px;font-size:14px;line-height:20px;color:#333}

.reload{left:552px;top:2302px}

/* footer */
.footer{left:0;top:2359px;width:1200px;height:161px;background:var(--footer)}
.footer-bar{left:0;top:2520px;width:1200px;height:51px;background:var(--footer-bottom)}
.foot-title{font-size:14px;color:var(--blue-bright);font-weight:400;letter-spacing:.3px}
.foot-list{list-style:none;font-size:10px;color:var(--footer-text);line-height:19px}
.foot-list li::before{content:"•";margin-right:7px;color:var(--footer-text)}
.news-input{left:778px;top:2421px;width:196px;height:34px;background:#d9d9d9;font-size:10.5px;color:#555;padding-left:10px;line-height:34px}
.news-btn{left:979px;top:2421px;width:86px;height:34px;background:#2e8ef0;color:var(--white);font-size:10.5px;display:flex;align-items:center;justify-content:center}
.copyright{left:132px;top:2538px;font-size:10px;color:var(--footer-text)}
.social{left:918px;top:2538px;display:flex;gap:20px;align-items:center}
.social span{width:12px;height:12px;border-radius:50%;background:#9a9a9a}
</style>
</head>
<body>
<div class="page">

  <!-- hero -->
  <div class="abs hero" role="img" aria-label="Blue-tinted photo of a man reading at a desk in front of bookshelves"></div>
  <div class="abs hero-shade"></div>
  <div class="abs menu-btn"><span></span><span></span><span></span></div>
  <div class="abs brand"><div class="brand-dot"></div><div class="brand-name">Venlotix</div></div>
  <div class="abs search">
    <div class="search-input">Search</div>
    <div class="search-btn"><svg width="14" height="14" viewBox="0 0 14 14"><circle cx="6" cy="6" r="4.3" fill="none" stroke="#fff" stroke-width="1.8"/><line x1="9" y1="9" x2="12.5" y2="12.5" stroke="#fff" stroke-width="2"/></svg></div>
  </div>
  <div class="abs hero-copy">
    <div class="lead">The Best Product and Service</div>
    <div class="title">REVIEWS AND RANKINGS</div>
  </div>
  <div class="abs hero-actions">
    <div class="hero-btn" style="width:88px">REGISTER</div>
    <div class="hero-btn" style="width:88px">LOG IN</div>
  </div>
  <div class="abs hero-dots"><span class="on"></span><span></span><span></span><span></span></div>

  <!-- category sidebar -->
  <nav class="abs sidebar">
    <div class="cat active"><svg viewBox="0 0 14 14"><path d="M1 7 7 1.5 13 7H11V13H8.5V9H5.5V13H3V7Z" fill="#0355a3"/></svg>HOME</div>
    <div class="cat"><svg viewBox="0 0 14 14"><rect x="1.5" y="2" width="11" height="10" fill="none" stroke="#777" stroke-width="1.4"/><line x1="7" y1="2" x2="7" y2="12" stroke="#777" stroke-width="1.4"/></svg>APPLIANCES</div>
    <div class="cat"><svg viewBox="0 0 14 14"><rect x="1" y="2" width="12" height="8" fill="none" stroke="#777" stroke-width="1.4"/><rect x="5" y="11" width="4" height="1.6" fill="#777"/></svg>COMPUTERS</div>
    <div class="cat"><svg viewBox="0 0 14 14"><circle cx="7" cy="5.5" r="3.6" fill="none" stroke="#777" stroke-width="1.4"/><rect x="5.5" y="10" width="3" height="2.5" fill="#777"/></svg>ELECTRONICS</div>
    <div class="cat"><svg viewBox="0 0 14 14"><path d="M4 6V4.5a3 3 0 0 1 6 0V6" fill="none" stroke="#777" stroke-width="1.4"/><rect x="2.5" y="6" width="9" height="7" fill="#777"/></svg>HOME SECURITY</div>
    <div class="cat"><svg viewBox="0 0 14 14"><rect x="4" y="1" width="6" height="12" rx="1" fill="none" stroke="#777" stroke-width="1.4"/></svg>MOBILE</div>
    <div class="cat"><svg viewBox="0 0 14 14"><circle cx="7" cy="7" r="4" fill="none" stroke="#777" stroke-width="2.4" stroke-dasharray="2 1.2"/><circle cx="7" cy="7" r="1.6" fill="#777"/></svg>SMART HOME</div>
    <div class="cat"><svg viewBox="0 0 14 14"><rect x="1" y="3" width="12" height="8" fill="none" stroke="#777" stroke-width="1.4"/><line x1="3" y1="6" x2="11" y2="6" stroke="#777"/><line x1="3" y1="8.5" x2="11" y2="8.5" stroke="#777"/></svg>SOFTWARE</div>
  </nav>

  <h2 class="abs section-title" style="left:327px;top:490px">New</h2>
  <h2 class="abs section-title" style="left:826px;top:490px">Popular</h2>

  <!-- feature 1 -->
  <article class="abs feature" style="top:545px">
    <div class="feature-media" role="img" aria-label="Bright living room with a grey sectional sofa and white shelving" style="background:linear-gradient(160deg,#e9e4dc,#cfc8bd 55%,#8f8b86)">
      <div class="tag" style="right:30px;bottom:0"><svg width="12" height="12" viewBox="0 0 14 14"><path d="M1 7 7 1.5 13 7H11V13H8.5V9H5.5V13H3V7Z" fill="#fff"/></svg></div>
      <div class="tag" style="right:2px;bottom:0"><svg width="12" height="12" viewBox="0 0 14 14"><path d="M1 7 7 1.5 13 7H11V13H8.5V9H5.5V13H3V7Z" fill="#fff"/></svg></div>
    </div>
    <p class="feature-text">Cum sociis natoque penatibus et magnis dis parturient montes, nascetur ridiculus mus. Aliquam accumsan nulla arcu.</p>
    <div class="author"><div class="avatar" role="img" aria-label="Author portrait" style="background:#b8a898"></div><div><div class="author-name">Mark Dalton</div><div class="author-date">10 August, 2016</div></div></div>
    <div class="minis">
      <div class="mini"><div class="mini-media" role="img" aria-label="Laptop and notebook on a wooden desk" style="background:linear-gradient(135deg,#a8937a,#6e5d4c)"><div class="tag" style="right:0;bottom:0"><svg width="12" height="12" viewBox="0 0 14 14"><path d="M1 7 7 1.5 13 7H11V13H8.5V9H5.5V13H3V7Z" fill="#fff"/></svg></div></div><p class="mini-text">Sed tristique, risus vitae aliquet mattis, felis metus sodales</p></div>
      <div class="mini"><div class="mini-media" role="img" aria-label="Young man using a phone outdoors" style="background:linear-gradient(135deg,#c9b48e,#7a8a5a)"><div class="tag" style="right:0;bottom:0"><svg width="12" height="12" viewBox="0 0 14 14"><path d="M1 7 7 1.5 13 7H11V13H8.5V9H5.5V13H3V7Z" fill="#fff"/></svg></div></div><p class="mini-text">Sed tristique, risus vitae aliquet mattis, felis metus sodales</p></div>
      <div class="mini"><div class="mini-media" role="img" aria-label="Source code on a dark screen" style="background:linear-gradient(135deg,#1d2a3a,#2c5b7a)"><div class="tag" style="right:0;bottom:0"><svg width="12" height="12" viewBox="0 0 14 14"><path d="M1 7 7 1.5 13 7H11V13H8.5V9H5.5V13H3V7Z" fill="#fff"/></svg></div></div><p class="mini-text">Sed tristique, risus vitae aliquet mattis, felis metus sodales</p></div>
    </div>
  </article>

  <!-- feature 2 -->
  <article class="abs feature" style="top:1130px">
    <div class="feature-media" role="img" aria-label="Home theatre with a flat TV, tall speakers and a dark cabinet" style="background:linear-gradient(180deg,#f1ece3,#e4dccf 70%,#c9bfae)">
      <div class="tag" style="right:30px;bottom:0"><svg width="12" height="12" viewBox="0 0 14 14"><path d="M1 7 7 1.5 13 7H11V13H8.5V9H5.5V13H3V7Z" fill="#fff"/></svg></div>
      <div class="tag" style="right:2px;bottom:0"><svg width="12" height="12" viewBox="0 0 14 14"><path d="M1 7 7 1.5 13 7H11V13H8.5V9H5.5V13H3V7Z" fill="#fff"/></svg></div>
    </div>
    <p class="feature-text">Cum sociis natoque penatibus et magnis dis parturient montes, nascetur ridiculus mus. Aliquam accumsan nulla arcu.</p>
    <div class="author"><div class="avatar" role="img" aria-label="Author portrait" style="background:#c9a98c"></div><div><div class="author-name">Mark Dalton</div><div class="author-date">10 August, 2016</div></div></div>
    <div class="minis">
      <div class="mini"><div class="mini-media" role="img" aria-label="Musician on a purple lit stage" style="background:linear-gradient(135deg,#3a1c6e,#c2307a)"><div class="tag" style="right:0;bottom:0"><svg width="12" height="12" viewBox="0 0 14 14"><path d="M1 7 7 1.5 13 7H11V13H8.5V9H5.5V13H3V7Z" fill="#fff"/></svg></div></div><p class="mini-text">Sed tristique, risus vitae aliquet mattis, felis metus sodales</p></div>
      <div class="mini"><div class="mini-media" role="img" aria-label="Hand touching glowing security icons" style="background:linear-gradient(135deg,#d9a64a,#2f9fb0)"><div class="tag" style="right:0;bottom:0"><svg width="12" height="12" viewBox="0 0 14 14"><path d="M1 7 7 1.5 13 7H11V13H8.5V9H5.5V13H3V7Z" fill="#fff"/></svg></div></div><p class="mini-text">Sed tristique, risus vitae aliquet mattis, felis metus sodales</p></div>
      <div class="mini"><div class="mini-media" role="img" aria-label="Smartphone controlling a smart home device" style="background:linear-gradient(135deg,#ecebe8,#b9b4ad)"><div class="tag" style="right:0;bottom:0"><svg width="12" height="12" viewBox="0 0 14 14"><path d="M1 7 7 1.5 13 7H11V13H8.5V9H5.5V13H3V7Z" fill="#fff"/></svg></div></div><p class="mini-text">Sed tristique, risus vitae aliquet mattis, felis metus sodales</p></div>
    </div>
  </article>

  <!-- feature 3 -->
  <article class="abs feature" style="top:1714px">
    <div class="feature-media" role="img" aria-label="Hands typing on a laptop showing a web dashboard" style="background:linear-gradient(140deg,#2a2622,#6d6a6b 45%,#b9a3c9 70%,#8a6a3e)">
      <div class="tag" style="right:30px;bottom:0"><svg width="12" height="12" viewBox="0 0 14 14"><path d="M1 7 7 1.5 13 7H11V13H8.5V9H5.5V13H3V7Z" fill="#fff"/></svg></div>
      <div class="tag" style="right:2px;bottom:0"><svg width="12" height="12" viewBox="0 0 14 14"><path d="M1 7 7 1.5 13 7H11V13H8.5V9H5.5V13H3V7Z" fill="#fff"/></svg></div>
    </div>
    <p class="feature-text">Cum sociis natoque penatibus et magnis dis parturient montes, nascetur ridiculus mus. Aliquam accumsan nulla arcu.</p>
    <div class="author"><div class="avatar" role="img" aria-label="Author portrait" style="background:#8f7b6a"></div><div><div class="author-name">Mark Dalton</div><div class="author-date">10 August, 2016</div></div></div>
    <div class="minis">
      <div class="mini"><div class="mini-media" role="img" aria-label="Headphones on a dark background" style="background:linear-gradient(135deg,#111,#5a5a5a)"><div class="tag" style="right:0;bottom:0"><svg width="12" height="12" viewBox="0 0 14 14"><path d="M1 7 7 1.5 13 7H11V13H8.5V9H5.5V13H3V7Z" fill="#fff"/></svg></div></div><p class="mini-text">Sed tristique, risus vitae aliquet mattis, felis metus sodales</p></div>
      <div class="mini"><div class="mini-media" role="img" aria-label="Blue circuit board close-up" style="background:linear-gradient(135deg,#0d3d73,#4aa3d8)"><div class="tag" style="right:0;bottom:0"><svg width="12" height="12" viewBox="0 0 14 14"><path d="M1 7 7 1.5 13 7H11V13H8.5V9H5.5V13H3V7Z" fill="#fff"/></svg></div></div><p class="mini-text">Sed tristique, risus vitae aliquet mattis, felis metus sodales</p></div>
      <div class="mini"><div class="mini-media" role="img" aria-label="Social network page on a screen" style="background:linear-gradient(135deg,#2f4f96,#8fa6d6)"><div class="tag" style="right:0;bottom:0"><svg width="12" height="12" viewBox="0 0 14 14"><path d="M1 7 7 1.5 13 7H11V13H8.5V9H5.5V13H3V7Z" fill="#fff"/></svg></div></div><p class="mini-text">Sed tristique, risus vitae aliquet mattis, felis metus sodales</p></div>
    </div>
  </article>

  <!-- popular -->
  <article class="abs popular" style="top:545px"><div class="pop-media" role="img" aria-label="White modern kitchen with marble island" style="background:linear-gradient(150deg,#e9e7e3,#a9a49c)"><div class="tag" style="right:0;bottom:0"><svg width="12" height="12" viewBox="0 0 14 14"><path d="M1 7 7 1.5 13 7H11V13H8.5V9H5.5V13H3V7Z" fill="#fff"/></svg></div></div><p class="pop-text">Donec hendrerit est finibus turpis aliquet, faucibus augue porta</p></article>
  <article class="abs popular" style="top:780px"><div class="pop-media" role="img" aria-label="Hands playing a digital piano" style="background:linear-gradient(150deg,#3a2c26,#171312)"><div class="tag" style="right:0;bottom:0"><svg width="12" height="12" viewBox="0 0 14 14"><path d="M2 5H5L9 2V12L5 9H2Z" fill="#fff"/></svg></div></div><p class="pop-text">Donec hendrerit est finibus turpis aliquet, faucibus augue porta</p></article>
  <article class="abs popular" style="top:1015px"><div class="pop-media" role="img" aria-label="Hand holding a phone with a home app near a staircase" style="background:linear-gradient(150deg,#a37d55,#4c3a2b)"><div class="tag" style="right:0;bottom:0"><svg width="12" height="12" viewBox="0 0 14 14"><circle cx="7" cy="7" r="4" fill="none" stroke="#fff" stroke-width="2.4" stroke-dasharray="2 1.2"/><circle cx="7" cy="7" r="1.6" fill="#fff"/></svg></div></div><p class="pop-text">Donec hendrerit est finibus turpis aliquet, faucibus augue porta</p></article>
  <article class="abs popular" style="top:1250px"><div class="pop-media" role="img" aria-label="Hand holding a smartphone against a colourful blurred background" style="background:linear-gradient(135deg,#1c6f9a,#9fd2c8 50%,#e3c25a)"><div class="tag" style="right:0;bottom:0"><svg width="12" height="12" viewBox="0 0 14 14"><rect x="4" y="1" width="6" height="12" rx="1" fill="none" stroke="#fff" stroke-width="1.5"/></svg></div></div><p class="pop-text">Donec hendrerit est finibus turpis aliquet, faucibus augue porta</p></article>
  <article class="abs popular" style="top:1485px"><div class="pop-media" role="img" aria-label="Woman using a wall-mounted smart control" style="background:linear-gradient(150deg,#eef1f3,#a9b7c2)"><div class="tag" style="right:0;bottom:0"><svg width="12" height="12" viewBox="0 0 14 14"><circle cx="7" cy="7" r="4" fill="none" stroke="#fff" stroke-width="2.4" stroke-dasharray="2 1.2"/><circle cx="7" cy="7" r="1.6" fill="#fff"/></svg></div></div><p class="pop-text">Donec hendrerit est finibus turpis aliquet, faucibus augue porta</p></article>
  <article class="abs popular" style="top:1720px"><div class="pop-media" role="img" aria-label="Hands holding a tablet" style="background:linear-gradient(150deg,#d9e6f1,#5f88b8)"><div class="tag" style="right:0;bottom:0"><svg width="12" height="12" viewBox="0 0 14 14"><rect x="4" y="1" width="6" height="12" rx="1" fill="none" stroke="#fff" stroke-width="1.5"/></svg></div></div><p class="pop-text">Donec hendrerit est finibus turpis aliquet, faucibus augue porta</p></article>

  <div class="abs reload"><svg width="22" height="22" viewBox="0 0 22 22" fill="none" stroke="#666" stroke-width="2.4"><path d="M4 10a7 7 0 0 1 12.5-4"/><path d="M18 12a7 7 0 0 1-12.5 4"/><path d="M17 2v4.5h-4.5" /><path d="M5 20v-4.5h4.5"/></svg></div>

  <!-- footer -->
  <footer class="abs footer"></footer>
  <div class="abs foot-title" style="left:132px;top:2388px">LINKS</div>
  <ul class="abs foot-list" style="left:132px;top:2413px"><li>Home</li><li>Appliances</li><li>Computers</li><li>Electronics</li></ul>
  <ul class="abs foot-list" style="left:245px;top:2413px"><li>Home Security</li><li>Mobile</li><li>Smart Home</li><li>Software</li></ul>
  <ul class="abs foot-list" style="left:365px;top:2413px"><li>Terms and Conditions</li><li>Privacy Policy</li><li>Sitemap</li></ul>
  <div class="abs foot-title" style="left:555px;top:2388px">CONTACT</div>
  <ul class="abs foot-list" style="left:555px;top:2413px"><li>Support</li><li>Email : info@venlotix.com</li></ul>
  <div class="abs foot-title" style="left:778px;top:2388px">NEWSLETTER SUBSCRIBE</div>
  <div class="abs news-input">Email Address</div>
  <div class="abs news-btn">SUBSCRIBE</div>

  <div class="abs footer-bar"></div>
  <div class="abs copyright">Copyright © 2016 Venlotix. All rights reserved.</div>
  <div class="abs social"><span></span><span></span><span></span><span></span>
    <svg width="16" height="12" viewBox="0 0 16 12"><rect x="0.5" y="0.5" width="15" height="11" fill="#9a9a9a"/><path d="M1 1 8 7 15 1" fill="none" stroke="#1b1b1b" stroke-width="1.3"/></svg>
  </div>
</div>
</body>
</html>
```